Business Cards for a law firm

Business cards for our law firm. Use our silhoette logo and OAK PARTNERS - check our website (www.oakpartners.example)

Contact Information for Business Card

our silhouette logo, OAK PARTNERS, 800-555-0147, Dorian Pemberton, dorian@oakpartners.example

Requirements
Must have
• our silhouette logo, OAK PARTNERS, 800-555-0147, Dorian Pemberton, dorian@oakpartners.example

```html
<!DOCTYPE html>
<html lang="en">
<head>
<meta charset="utf-8">
<title>Oak Partners — Business Cards</title>
<link href="https://fonts.googleapis.com/css2?family=Montserrat:wght@400;500&family=Open+Sans:wght@400;600;700&display=swap" rel="stylesheet">
<style>
  :root {
    --navy: #2b3a80;
    --navy-deep: #1f2b66;
    --navy-soft: #4a5aa6;
    --ink: #2f2f3a;
    --paper: #ffffff;
    --backdrop: #e8e5e0;
  }
  * { box-sizing: border-box; margin: 0; padding: 0; }
  html, body {
    width: 900px; height: 1200px; overflow: hidden;
    background: var(--backdrop);
  }
  .canvas { position: relative; width: 900px; height: 1200px; }

  .card {
    position: absolute; left: 126px; width: 648px; height: 468px;
    border-radius: 24px; overflow: hidden;
    box-shadow: 0 6px 18px rgba(0,0,0,.18);
  }
  .card--front { top: 66px; background: var(--paper); }
  .card--back { top: 666px; background: var(--navy); }

  .brand {
    display: flex; align-items: center; gap: 12px;
    font-family: "Montserrat", sans-serif; font-weight: 500;
    letter-spacing: 1px;
  }
  .brand__mark { width: 22px; height: 22px; }
  .card--front .brand { position: absolute; left: 38px; top: 66px; font-size: 30px; color: var(--navy); }
  .card--front .brand__mark { background: var(--navy); }

  .person { position: absolute; left: 38px; top: 250px; color: var(--navy); font-family: "Open Sans", sans-serif; }
  .person__name { font-size: 26px; font-weight: 700; }
  .person__role { font-size: 16px; color: var(--ink); margin-top: 2px; }

  .address { position: absolute; left: 38px; top: 320px; font-family: "Open Sans", sans-serif; font-size: 15px; line-height: 22px; color: var(--ink); }

  .contacts { position: absolute; left: 38px; top: 378px; list-style: none; font-family: "Open Sans", sans-serif; font-size: 15px; color: var(--ink); }
  .contacts li { display: flex; align-items: center; gap: 10px; height: 24px; }
  .contacts svg { width: 14px; height: 14px; }

  .figures-art {
    position: absolute; left: 372px; top: 30px; width: 246px; height: 408px;
    background: linear-gradient(180deg, var(--navy-soft) 0%, var(--navy) 100%);
    opacity: .85; border-radius: 6px;
  }

  .pattern-art {
    position: absolute; inset: 0;
    background: linear-gradient(180deg, var(--navy-soft) 0%, var(--navy) 55%, var(--navy-deep) 100%);
  }
  .card--back .brand {
    position: absolute; left: 200px; top: 225px; font-size: 32px; color: var(--paper);
  }
  .card--back .brand__mark { background: var(--paper); }
</style>
</head>
<body>
<div class="canvas">

  <section class="card card--front">
    <div class="brand"><span class="brand__mark"></span><span class="brand__name">OAK PARTNERS</span></div>

    <div class="person">
      <div class="person__name">Dorian Pemberton</div>
      <div class="person__role">Lawyer</div>
    </div>

    <address class="address">415 Cedar Lane, Suite 12<br>Brookfield, OH 43010</address>

    <ul class="contacts">
      <li>
        <svg viewBox="0 0 14 14" aria-hidden="true"><circle cx="7" cy="7" r="7" fill="var(--navy)"/><path d="M4.5 3.5l1.6 0 .6 1.8-1 .8a5 5 0 0 0 2.2 2.2l.8-1 1.8.6 0 1.6c-3.6.3-6.3-2.4-6-6z" fill="#fff"/></svg>
        <span>800-555-0147</span>
      </li>
      <li>
        <svg viewBox="0 0 14 14" aria-hidden="true"><rect x="1" y="3" width="12" height="8" rx="1" fill="var(--navy)"/><path d="M1.5 3.5L7 7.5l5.5-4" stroke="#fff" stroke-width="1" fill="none"/></svg>
        <span>dorian@oakpartners.example</span>
      </li>
      <li>
        <svg viewBox="0 0 14 14" aria-hidden="true"><circle cx="7" cy="7" r="6.5" fill="var(--navy)"/><g stroke="#fff" stroke-width=".9" fill="none"><ellipse cx="7" cy="7" rx="2.6" ry="6"/><path d="M1 7h12M2 4h10M2 10h10"/></g></svg>
        <span>www.oakpartners.example</span>
      </li>
    </ul>

    <div class="figures-art" role="img" aria-label="Silhouette illustration of two standing men in suits"></div>
  </section>

  <section class="card card--back">
    <div class="pattern-art" role="img" aria-label="Repeating pattern of small standing figure silhouettes in shades of blue"></div>
    <div class="brand"><span class="brand__mark"></span><span class="brand__name">OAK PARTNERS</span></div>
  </section>

</div>
</body>
</html>
```